Kitchen and custom cabinetry company looking for business card design

We make: * Custom Kitchens, contemporary and traditional kitchens, Vanities, Libraries, Custom Entry Doors, Custom Wine Cellars and Custom Design Furniture. Phone number 555-284-7716. Address: Westhampton NY. Email: KAVRO@mailbox.example Portfolio at: KAVROcabinetry.example I would like moderns fonts and not heavy lines. double side but maybe will use clear plastic. I attached the logo.

Industry/Entity Type

Business

```html
<!DOCTYPE html>
<html lang="en">
<head>
<meta charset="utf-8">
<title>Kavro Cabinetry – Business Card</title>
<link rel="stylesheet" href="https://fonts.googleapis.com/css2?family=Questrial&display=swap">
<style>
  :root {
    --orange: #f15a29;
    --orange-soft: #f5845c;
    --grey: #808080;
    --grey-soft: #b5b5b5;
    --logo-grey: #7a7a7a;
    --white: #ffffff;
    --backdrop: #e8e3dc;
  }
  * { margin: 0; padding: 0; box-sizing: border-box; }
  html, body {
    width: 1200px; height: 970px; overflow: hidden;
    background: var(--backdrop);
    font-family: "Questrial", "Helvetica Neue", Arial, sans-serif;
  }
  .canvas { position: relative; width: 1200px; height: 970px; }
  .card { position: absolute; top: 163px; width: 409px; height: 714px; }
  .card--front { left: 167px; --accent: var(--orange); --accent-soft: var(--orange-soft); }
  .card--back  { left: 627px; --accent: var(--grey);   --accent-soft: var(--grey-soft); }

  .card__cap {
    height: 30px; background: var(--accent);
    border-radius: 22px 22px 0 0;
  }
  .card__logo-area {
    height: 268px; background: var(--white);
    display: flex; align-items: center; justify-content: center;
  }
  .wordmark { display: flex; align-items: center; gap: 16px; color: var(--logo-grey); }
  .wordmark__square { width: 22px; height: 22px; background: var(--orange); }
  .wordmark__text { display: flex; flex-direction: column; line-height: 1; }
  .wordmark__name { font-size: 64px; letter-spacing: 4px; }
  .wordmark__sub { font-size: 19px; letter-spacing: 7px; margin-top: 6px; }

  .card__strip { margin-top: 26px; height: 47px; background: var(--accent-soft); }

  .card__panel {
    margin-top: 24px; height: 319px; background: var(--accent);
    border-radius: 0 0 22px 22px;
    color: var(--white); text-align: right;
    padding: 42px 40px 0 0;
  }
  .contact__name { font-size: 25px; font-weight: 700; line-height: 30px; }
  .contact__role { font-size: 19px; line-height: 27px; margin-bottom: 20px; }
  .contact__line { font-size: 19px; line-height: 27px; }
  .contact__address { margin-top: 20px; font-size: 19px; line-height: 27px; }

  .services { list-style: none; padding-top: 56px; }
  .services__item { font-size: 20px; line-height: 27px; text-transform: uppercase; }
</style>
</head>
<body>
<main class="canvas">

  <section class="card card--front" aria-label="Card front">
    <div class="card__cap"></div>
    <div class="card__logo-area">
      <div class="wordmark">
        <span class="wordmark__square"></span>
        <span class="wordmark__text">
          <span class="wordmark__name">KAVRO</span>
          <span class="wordmark__sub">CABINETRY INC.</span>
        </span>
      </div>
    </div>
    <div class="card__strip"></div>
    <div class="card__panel">
      <p class="contact__name">Marco Delvane</p>
      <p class="contact__role">Owner</p>
      <p class="contact__line">555-284-7716</p>
      <p class="contact__line">kavro@mailbox.example</p>
      <p class="contact__line">www.kavrocabinetry.example</p>
      <p class="contact__address">2207 Harbor Pond rd,<br>Westhampton, NY, 11977</p>
    </div>
  </section>

  <section class="card card--back" aria-label="Card back">
    <div class="card__cap"></div>
    <div class="card__logo-area">
      <div class="wordmark">
        <span class="wordmark__square"></span>
        <span class="wordmark__text">
          <span class="wordmark__name">KAVRO</span>
          <span class="wordmark__sub">CABINETRY INC.</span>
        </span>
      </div>
    </div>
    <div class="card__strip"></div>
    <div class="card__panel">
      <ul class="services">
        <li class="services__item">Contemporay Kitchens</li>
        <li class="services__item">Traditional Kitchens</li>
        <li class="services__item">Vanities</li>
        <li class="services__item">Libraries</li>
        <li class="services__item">Custom Wine Cellars</li>
        <li class="services__item">Custom Design Furniture</li>
      </ul>
    </div>
  </section>

</main>
</body>
</html>
```